Help our Sugar Loom find our winning design! We're looking for a business card....

We’re a Sugar Loom in NY specializing in custom-made cakes and unique desserts.
Our cakes combine flavor and art, each designed to match customer’s special event and theme.
We’d like a unique business card with a clean design that will combine French chic and artistic look & feel.
We’d like to differentiate ourselves from standard bakeries, please don’t offer cupcake images :-)
Our logo is peach-pink and brown and we’d love to use these colors ( . Another color that can be added is gold - or feel free to suggest!

Target Market(s)

Women, ages 25-55

Industry/Entity Type

Boutique

Contact Information for Business Card

Text on card:
Logo
Sugar Loom by Dana Welch

www.sugarloomsweets.com
hello@sugarloom.com
(516) 555-0147
F – sugarloomnyc
IG - sugarloom_ny

Font styles to use
Sans Serif
Script

Requirements
Must have
• Logo
• Clean look
• French chic and artistic look & feel.
Nice to have
• Damask pattern
Should not have
• Cupcake images

```html
<!DOCTYPE html>
<html lang="en">
<head>
<meta charset="utf-8">
<title>Sugar Loom – Business Card</title>
<link href="https://fonts.googleapis.com/css2?family=Exo+2:wght@400;600&display=swap" rel="stylesheet">
<style>
  :root {
    --backdrop: #e9e6e4;
    --card-white: #ffffff;
    --card-grey: #6f6b69;
    --petal-pink: #f28ea6;
    --logo-pink: #e98aa0;
    --text-light: #ffffff;
    --text-dark: #4a4443;
    --shadow: rgba(0, 0, 0, 0.18);
  }
  * { box-sizing: border-box; margin: 0; padding: 0; }
  html, body {
    width: 1200px;
    height: 901px;
    overflow: hidden;
    background: var(--backdrop);
    font-family: "Exo 2", sans-serif;
  }
  .sheet {
    position: relative;
    width: 1200px;
    height: 901px;
    display: flex;
    align-items: center;
    justify-content: center;
    gap: 70px;
  }
  .card {
    position: relative;
    width: 525px;
    height: 300px;
    border-radius: 26px;
    overflow: hidden;
    box-shadow: 0 14px 30px var(--shadow);
    background: var(--card-white);
  }
  .card-back .shape-layer {
    position: absolute;
    inset: 0;
  }
  .card-back .brand-name {
    position: absolute;
    left: 22px;
    top: 126px;
    width: 150px;
    text-align: center;
    font-size: 22px;
    font-weight: 600;
    color: var(--logo-pink);
    letter-spacing: 0.5px;
  }
  .contact-block {
    position: absolute;
    right: 30px;
    top: 30px;
    text-align: right;
    color: var(--text-light);
  }
  .contact-name {
    font-size: 19px;
    font-weight: 600;
    letter-spacing: 1.5px;
    text-transform: uppercase;
  }
  .contact-role {
    font-size: 14px;
    margin-top: 3px;
  }
  .contact-address {
    font-size: 13px;
    line-height: 1.45;
    margin-top: 24px;
    padding-right: 24px;
  }
  .contact-list {
    list-style: none;
    margin-top: 20px;
    font-size: 13px;
    line-height: 1;
  }
  .contact-list li {
    display: flex;
    align-items: center;
    justify-content: flex-end;
    gap: 9px;
    margin-bottom: 9px;
  }
  .contact-list .icon {
    width: 14px;
    height: 14px;
    fill: none;
    stroke: var(--text-light);
    stroke-width: 1.6;
  }
  .card-front {
    display: flex;
    align-items: center;
    justify-content: center;
  }
  .card-front .brand-name {
    font-size: 44px;
    font-weight: 600;
    color: var(--logo-pink);
    letter-spacing: 1px;
  }
</style>
</head>
<body>
<main class="sheet">

  <section class="card card-back" aria-label="Business card back">
    <svg class="shape-layer" viewBox="0 0 525 300" width="525" height="300" aria-hidden="true">
      <rect width="525" height="300" fill="var(--card-white)"/>
      <path d="M196 0 C 262 60, 270 200, 200 300 L 525 300 L 525 0 Z" fill="var(--petal-pink)"/>
      <path d="M216 0 C 286 64, 292 206, 224 300 L 525 300 L 525 0 Z" fill="var(--card-grey)"/>
    </svg>

    <p class="brand-name">Sugar Loom</p>

    <div class="contact-block">
      <h1 class="contact-name">Dana Welch</h1>
      <p class="contact-role">Managing Director</p>
      <p class="contact-address">214 Bleecker Street<br>New York NY</p>
      <ul class="contact-list">
        <li>(516) 555-0147
          <svg class="icon" viewBox="0 0 16 16"><path d="M4 2 L6 2 L7 5 L5.5 6.5 C6.5 8.5 7.5 9.5 9.5 10.5 L11 9 L14 10 L14 12 C14 13 13 14 12 14 C7 14 2 9 2 4 C2 3 3 2 4 2 Z"/></svg>
        </li>
        <li>(516) 555-0148
          <svg class="icon" viewBox="0 0 16 16"><rect x="4.5" y="1.5" width="7" height="13" rx="1.2"/><line x1="7" y1="12.3" x2="9" y2="12.3"/></svg>
        </li>
        <li>hello@sugarloom.com
          <svg class="icon" viewBox="0 0 16 16"><rect x="1.5" y="3.5" width="13" height="9" rx="1"/><path d="M1.5 4 L8 9 L14.5 4"/></svg>
        </li>
        <li>www.sugarloomsweets.com
          <svg class="icon" viewBox="0 0 16 16"><circle cx="8" cy="8" r="6.3"/><ellipse cx="8" cy="8" rx="2.8" ry="6.3"/><line x1="1.7" y1="8" x2="14.3" y2="8"/></svg>
        </li>
      </ul>
    </div>
  </section>

  <section class="card card-front" aria-label="Business card front">
    <p class="brand-name">Sugar Loom</p>
  </section>

</main>
</body>
</html>
```